Business Cards for company that supports physicians that do medical research

Need to create a business card for Qorvel Studies (www.qorvelstudies.example), a company devoted to supporting physicians who conduct medical research. The form of the card should match the message of research and information quest. I have provided the logo of the company as an uploaded file. Designs should be simple and slick aimed at very high end clients.

Target Market(s)

Medical doctors that are also researchers

Industry/Entity Type

Medical

Contact Information for Business Card

Should feature logo and fields for personal info:
Name/title
Phone /email

Font styles to use
Serif
Sans Serif

Requirements
Must have
• Qorvel logo and fields for personal info:
• Name: Bertrand Okonfu
• Title: VP Research and Senior Analyst
• Phone: 555-203-4719
• email: info@qorvelstudies.example
Nice to have
• Interesting cards that I've seen:
• 1- all black/charcoal or very dark background
• 2- Plastic - semi-transparent
• 3- non-standard height-width ratios
• 4- Functional cards -- USB drive incorporated
Should not have
• Too busy; needs to stay very simple

```html
<!DOCTYPE html>
<html lang="en">
<head>
<meta charset="utf-8">
<title>Qorvel Studies – Business Cards</title>
<link rel="stylesheet" href="https://fonts.googleapis.com/css2?family=Montserrat:wght@500&family=Open+Sans:wght@400;600&display=swap">
<style>
  :root {
    --backdrop: #a9a7a8;
    --card: #2b2d31;
    --card-light: #3a3c41;
    --card-dark: #222327;
    --accent-blue: #2a90d8;
    --text-light: #f2f3f4;
    --text-soft: #d9dbde;
  }
  * { margin: 0; padding: 0; box-sizing: border-box; }
  html, body {
    width: 1200px; height: 1200px; overflow: hidden;
    background: var(--backdrop);
  }
  .canvas { position: relative; width: 1200px; height: 1200px; }
  .card {
    position: absolute;
    width: 712px; height: 418px;
    border-radius: 24px;
    overflow: hidden;
    background: var(--card);
  }
  .card--front { left: 238px; top: 118px; }
  .card--back  { left: 231px; top: 644px; }
  .card__photo {
    position: absolute; inset: 0;
    background: linear-gradient(125deg, var(--card-dark) 0%, var(--card) 45%, var(--card-light) 75%, var(--card) 100%);
  }
  .wordmark {
    position: absolute;
    font-family: "Open Sans", sans-serif;
    font-weight: 600;
    color: var(--text-light);
    letter-spacing: 3px;
    white-space: nowrap;
  }
  .card--front .wordmark {
    left: 0; right: 0; top: 172px;
    text-align: center; font-size: 44px;
  }
  .card--back .wordmark {
    right: 40px; top: 300px; font-size: 36px;
  }
  .person { position: absolute; left: 48px; top: 44px; }
  .person__name {
    font-family: "Montserrat", sans-serif;
    font-weight: 500; font-size: 22px;
    color: var(--accent-blue);
    letter-spacing: 0.3px;
  }
  .person__title {
    margin-top: 8px;
    font-family: "Open Sans", sans-serif;
    font-size: 15px; color: var(--text-soft);
  }
  .contacts {
    position: absolute; left: 48px; top: 296px;
    list-style: none;
    font-family: "Open Sans", sans-serif;
    font-size: 17px; color: var(--text-light);
  }
  .contacts li {
    display: flex; align-items: center;
    height: 26.5px;
  }
  .contacts svg { width: 16px; height: 16px; margin-right: 16px; flex: none; }
  .contacts svg * { fill: var(--accent-blue); }
</style>
</head>
<body>
<main class="canvas">
  <section class="card card--front">
    <div class="card__photo" role="img" aria-label="Dark toned photo of a stethoscope resting on a keyboard beside a pen"></div>
    <div class="wordmark">Qorvel Studies</div>
  </section>

  <section class="card card--back">
    <div class="card__photo" role="img" aria-label="Dark toned photo of a stethoscope resting on a keyboard beside a pen"></div>
    <div class="person">
      <h1 class="person__name">Bertrand Okonfu</h1>
      <p class="person__title">VP Research &amp; Senior Analyst</p>
    </div>
    <ul class="contacts">
      <li>
        <svg viewBox="0 0 16 16" aria-hidden="true"><path d="M1 5c0-2 2-3 7-3s7 1 7 3v1h-4V4.5H5V6H1z"/><path d="M3 7h10l1 7H2z"/></svg>
        555-203-4719
      </li>
      <li>
        <svg viewBox="0 0 16 16" aria-hidden="true"><path d="M1 3h14v10H1z M2.5 4.5 8 9l5.5-4.5z" fill-rule="evenodd"/></svg>
        info@qorvelstudies.example
      </li>
      <li>
        <svg viewBox="0 0 16 16" aria-hidden="true"><path fill-rule="evenodd" d="M8 1a7 7 0 1 1 0 14A7 7 0 0 1 8 1zm-1 2.2A5 5 0 0 0 3.1 7H5.6A11 11 0 0 1 7 3.2zm2 0A11 11 0 0 1 10.4 7h2.5A5 5 0 0 0 9 3.2zM6.7 7h2.6A9 9 0 0 0 8 3.4 9 9 0 0 0 6.7 7zm-3.6 2A5 5 0 0 0 7 12.8 11 11 0 0 1 5.6 9zm3.6 0A9 9 0 0 0 8 12.6 9 9 0 0 0 9.3 9zm3.7 0A11 11 0 0 1 9 12.8 5 5 0 0 0 12.9 9z"/></svg>
        www.qorvelstudies.example
      </li>
    </ul>
    <div class="wordmark">Qorvel Studies</div>
  </section>
</main>
</body>
</html>
```